Commercial Real Estate

We need a business card design for a new commercial real estate business that specializes in apartment building brokerage. Not individual units but the entire complex. We find and represent the owners existing buildings and well as new buyers for those buildings. The design should convey trust, integrity, knowledge and growth. It should be easily read.

Target Market(s)

40 to 65 years old

Industry/Entity Type

Real Estate

```html
<!DOCTYPE html>
<html lang="en">
<head>
<meta charset="utf-8">
<title>Brightwell – Business Card</title>
<link href="https://fonts.googleapis.com/css2?family=Open+Sans:wght@400;600;700&display=swap" rel="stylesheet">
<style>
  :root {
    --backdrop: #e4e5e5;
    --slate: #5b6a68;
    --teal: #5fcac3;
    --paper: #ffffff;
    --ink-light: #ffffff;
  }
  html, body {
    margin: 0;
    width: 1200px;
    height: 899px;
    overflow: hidden;
    background: var(--backdrop);
    font-family: "Open Sans", Arial, sans-serif;
  }
  .canvas {
    position: relative;
    width: 1200px;
    height: 899px;
  }
  .card {
    position: absolute;
    left: 320px;
    width: 560px;
    height: 320px;
    background: var(--paper);
    overflow: hidden;
    box-shadow: 0 6px 18px rgba(0,0,0,0.15);
  }
  .card--back { top: 90px; }
  .card--front { top: 480px; }
  .card__shapes {
    position: absolute;
    inset: 0;
    width: 560px;
    height: 320px;
  }
  .shape-slate { fill: var(--slate); }
  .shape-band { fill: none; stroke: var(--teal); stroke-width: 9; }

  .brand {
    position: absolute;
    display: flex;
    align-items: center;
    gap: 10px;
    color: var(--slate);
    font-weight: 700;
    letter-spacing: 3px;
    text-transform: uppercase;
    white-space: nowrap;
  }
  .brand__square {
    width: 16px;
    height: 16px;
    background: var(--teal);
  }
  .card--front .brand { left: 34px; top: 52px; font-size: 22px; letter-spacing: 2px; }
  .card--front .brand__square { width: 14px; height: 14px; }
  .card--back .brand { left: 330px; top: 150px; font-size: 24px; }

  .website {
    position: absolute;
    right: 26px;
    bottom: 22px;
    color: var(--slate);
    font-size: 13px;
  }

  .contact {
    position: absolute;
    left: 300px;
    top: 52px;
    color: var(--ink-light);
    font-size: 13px;
    line-height: 1.45;
  }
  .contact__name {
    margin: 0;
    font-size: 19px;
    font-weight: 700;
    line-height: 1.2;
  }
  .contact__title {
    margin: 0 0 16px;
    font-size: 16px;
  }
  .contact__address { margin: 0 0 6px; }
  .contact__lines { margin: 0; }
  .contact__label { font-weight: 700; }
</style>
</head>
<body>
<main class="canvas">

  <section class="card card--back" aria-label="Business card back">
    <svg class="card__shapes" viewBox="0 0 560 320" aria-hidden="true">
      <path class="shape-slate" d="M0 0 H360 C300 140 190 250 40 320 H0 Z"/>
      <path class="shape-band" d="M368 -4 C308 144 196 256 46 326"/>
    </svg>
    <div class="brand"><span class="brand__square"></span>Brightwell</div>
    <div class="website">www.example.com</div>
  </section>

  <section class="card card--front" aria-label="Business card front">
    <svg class="card__shapes" viewBox="0 0 560 320" aria-hidden="true">
      <path class="shape-slate" d="M330 0 H560 V320 H0 V262 C140 226 268 128 330 0 Z"/>
      <path class="shape-band" d="M325 -4 C262 124 136 222 -4 257"/>
    </svg>
    <div class="brand"><span class="brand__square"></span>Brightwell</div>
    <div class="contact">
      <p class="contact__name">Dana Whitfield</p>
      <p class="contact__title">Consultant</p>
      <p class="contact__address">214, 9th floor,<br>Harbor Point<br>Avenue</p>
      <p class="contact__lines">
        <span class="contact__label">Ph:</span> 555 014 2280<br>
        <span class="contact__label">Cell:</span> 555 014 2281<br>
        <span class="contact__label">Fax:</span> 555 014 2282<br>
        <span class="contact__label">Email:</span> dana@example.com<br>
        www.example.com
      </p>
    </div>
  </section>

</main>
</body>
</html>
```